LHP Regal Business Card Design 2020

Your Manor Steward is looking for a business card that is clean and straight to the point but still looks high-end and attractive. We are a team comprised of management and field professionals focused on the high-end residential marketplace. We serve homeowners and trade professionals directly based out of the Metrowest/Boston area. We provide client services as well as construction/renovation services.
We are aiming for a black and white feel (white background and black text) and a matte finish with rounded edges.

We want to emphasis our vision of "Properties - Projects - Partners".
Dana Pellham is the president of LHP

Please include the following areas we service: Boston/Cape/Newport
Please make sure to include Dana's mobile (555) 213 4480 & office number (555) 640 1937, email dana@yourmanorsteward.example and website www.yourmanorsteward.example

Colors

Designer to choose only greyscale colors for use in the design.

Requirements
Must have
• Include "Properties - Projects - Partners" in design

Include "After Hours Emergency Support # 1800 555 0142" with icon

```html
<!DOCTYPE html>
<html lang="en">
<head>
<meta charset="utf-8">
<title>LHP Business Card</title>
<link href="https://fonts.googleapis.com/css2?family=Montserrat:wght@400;500;600;700;800&display=swap" rel="stylesheet">
<style>
  :root {
    --stage: #2a2a2a;
    --ink: #1a1a1a;
    --card-black: #161616;
    --card-white: #ffffff;
    --text-light: #f2f2f2;
    --text-muted: #cfcfcf;
    --text-body: #2b2b2b;
    --rule: #9a9a9a;
  }
  * { box-sizing: border-box; margin: 0; padding: 0; }
  html, body {
    width: 1200px; height: 930px; overflow: hidden;
    background: var(--stage);
    font-family: "Montserrat", sans-serif;
  }
  .stage {
    width: 1200px; height: 930px;
    display: flex; flex-direction: column; align-items: center;
    justify-content: center; gap: 34px;
  }
  .card {
    width: 680px; height: 388px; border-radius: 22px;
    position: relative; overflow: hidden;
  }

  /* Back side */
  .card-back { background: var(--card-black); color: var(--text-light); }
  .back-brand {
    position: absolute; top: 60px; left: 0; right: 0; text-align: center;
  }
  .brand-mark {
    display: inline-flex; align-items: center; gap: 14px;
    font-weight: 800; font-size: 104px; line-height: 1; letter-spacing: -2px;
  }
  .brand-mark .dot { width: 22px; height: 22px; background: currentColor; }
  .brand-name {
    margin-top: 10px; font-weight: 700; font-size: 17px; letter-spacing: 2.4px;
  }
  .service-title {
    position: absolute; top: 236px; left: 0; right: 0; text-align: center;
    font-weight: 700; font-size: 19px; letter-spacing: 2px;
  }
  .service-areas {
    position: absolute; top: 282px; left: 0; right: 0; text-align: center;
    font-weight: 400; font-size: 18px; letter-spacing: 1.6px; color: var(--text-muted);
  }
  .emergency {
    position: absolute; bottom: 30px; left: 0; right: 0;
    display: flex; align-items: center; justify-content: center; gap: 9px;
    font-weight: 500; font-size: 14px; letter-spacing: 1px; color: var(--text-muted);
  }
  .emergency svg { width: 14px; height: 14px; flex: none; }

  /* Front side */
  .card-front { background: var(--card-white); color: var(--text-body); }
  .front-brand {
    position: absolute; left: 36px; top: 110px; width: 280px; text-align: center;
    color: var(--ink);
  }
  .front-brand .brand-mark { font-size: 90px; }
  .front-brand .brand-name { font-size: 15px; letter-spacing: 2px; }
  .divider {
    position: absolute; left: 342px; top: 70px; width: 1px; height: 190px;
    background: var(--rule);
  }
  .contact { position: absolute; left: 366px; top: 76px; right: 24px; }
  .person-name {
    font-weight: 700; font-size: 24px; letter-spacing: 1.4px; color: var(--ink);
  }
  .person-role { font-size: 14px; margin-top: 2px; margin-bottom: 14px; }
  .contact-list { list-style: none; }
  .contact-list li {
    display: flex; align-items: center; gap: 9px;
    font-size: 14px; line-height: 25px; white-space: nowrap;
  }
  .contact-list svg { width: 13px; height: 13px; flex: none; }
  .vision-band {
    position: absolute; left: 0; right: 0; bottom: 0; height: 62px;
    background: var(--card-black); color: var(--text-light);
    display: flex; align-items: center; justify-content: flex-end; padding-right: 40px;
    font-weight: 600; font-size: 21px; letter-spacing: 1.6px;
  }
</style>
</head>
<body>
<main class="stage">
  <section class="card card-back" aria-label="Card back">
    <div class="back-brand">
      <div class="brand-mark"><span class="dot"></span>LHP</div>
      <div class="brand-name">YOUR MANOR STEWARD</div>
    </div>
    <div class="service-title">WE SERVICE</div>
    <div class="service-areas">BOSTON | METROWEST | SOUTH SHORE | CAPE/NEWPORT</div>
    <div class="emergency">
      <svg viewBox="0 0 16 16" aria-hidden="true"><path fill="currentColor" d="M3.6 1l2.3 2.6-1.3 2.2a9 9 0 0 0 5.6 5.6l2.2-1.3L15 12.4 13.4 15C6.8 15 1 9.2 1 2.6z"/></svg>
      After Hours Emergency Support # 1800 555 0142
    </div>
  </section>

  <section class="card card-front" aria-label="Card front">
    <div class="front-brand">
      <div class="brand-mark"><span class="dot"></span>LHP</div>
      <div class="brand-name">YOUR MANOR STEWARD</div>
    </div>
    <div class="divider"></div>
    <div class="contact">
      <div class="person-name">DANA PELLHAM</div>
      <div class="person-role">President</div>
      <ul class="contact-list">
        <li>
          <svg viewBox="0 0 16 16" aria-hidden="true"><path fill="currentColor" d="M3.6 1l2.3 2.6-1.3 2.2a9 9 0 0 0 5.6 5.6l2.2-1.3L15 12.4 13.4 15C6.8 15 1 9.2 1 2.6z"/></svg>
          (555) 213 4480
        </li>
        <li>
          <svg viewBox="0 0 16 16" aria-hidden="true"><rect x="4" y="1" width="8" height="14" rx="1.5" fill="none" stroke="currentColor" stroke-width="1.6"/><circle cx="8" cy="12.3" r="0.9" fill="currentColor"/></svg>
          (555) 640 1937
        </li>
        <li>
          <svg viewBox="0 0 16 16" aria-hidden="true"><rect x="1.5" y="3.5" width="13" height="9" fill="none" stroke="currentColor" stroke-width="1.5"/><path d="M1.5 3.5L8 9l6.5-5.5" fill="none" stroke="currentColor" stroke-width="1.5"/></svg>
          dana@yourmanorsteward.example
        </li>
        <li>
          <svg viewBox="0 0 16 16" aria-hidden="true"><g fill="none" stroke="currentColor" stroke-width="1.3"><circle cx="8" cy="8" r="6.5"/><ellipse cx="8" cy="8" rx="2.8" ry="6.5"/><path d="M1.5 8h13M2.6 4.6h10.8M2.6 11.4h10.8"/></g></svg>
          www.yourmanorsteward.example
        </li>
      </ul>
    </div>
    <div class="vision-band">PROPERTIES - PROJECTS - PARTNERS</div>
  </section>
</main>
</body>
</html>
```